Ward Compass Business Card Design*

We need a business card design for our company Ward Compass. Our company is specialized in providing online consulting services regarding medical institutions, hospitals and doctors. We work with patients worldwide looking to choose between healthcare providers. We have a website you may use as a reference, where we list doctors and clinics worldwide. So we target Medical providers as well as patients worldwide.
Target Market(s)
Medical Providers and patients around the world
Industry/Entity Type
Medical
Contact Information for Business Card
Salwa Kettani
CEO
+90 612 348 2175
info@wardcompass.example
www.wardcompass.example
14 Annakhil 7 H.R.B. Rabat, Morocco
Requirements
Must have
- Company logo/name on one full side, personal info and smaller logo and company name on the other side.
Nice to have
- Smart and elegant design

```html
<!DOCTYPE html>
<html lang="en">
<head>
<meta charset="utf-8">
<title>Ward Compass — Business Card</title>
<link rel="stylesheet" href="https://fonts.googleapis.com/css2?family=Quicksand:wght@400;500;700&display=swap">
<style>
  :root {
    --backdrop: #0e0e0f;
    --card: #2a2b2c;
    --card-edge: #333435;
    --silver: #cfd1d3;
    --silver-soft: #9a9c9e;
    --text-muted: #8a8c8e;
  }
  * { box-sizing: border-box; margin: 0; padding: 0; }
  html, body {
    width: 1200px; height: 900px; overflow: hidden;
    background: var(--backdrop);
    font-family: "Quicksand", sans-serif;
  }
  .canvas {
    position: relative; width: 1200px; height: 900px;
    display: flex; align-items: center; justify-content: center; gap: 50px;
  }
  .card {
    position: relative; width: 525px; height: 300px;
    background: var(--card);
    border: 1px solid var(--card-edge);
    border-radius: 3px;
    color: var(--silver);
  }

  /* Back: personal details */
  .card-back .brand {
    position: absolute; left: 34px; top: 34px;
    display: flex; align-items: center; gap: 10px;
    font-size: 21px; font-weight: 500; letter-spacing: 0.08em;
    text-transform: uppercase; color: var(--silver);
  }
  .brand-dot {
    width: 26px; height: 26px; border-radius: 50%;
    background: var(--silver);
  }
  .address {
    position: absolute; left: 34px; top: 100px;
    font-size: 13px; line-height: 1.45; color: var(--text-muted);
  }
  .contacts {
    position: absolute; left: 34px; top: 160px;
    list-style: none; font-size: 13px; color: var(--text-muted);
  }
  .contacts li { display: flex; align-items: center; gap: 9px; line-height: 22px; }
  .contacts svg { width: 12px; height: 12px; fill: none; stroke: var(--silver); stroke-width: 1.6; }
  .person {
    position: absolute; right: 34px; top: 118px; text-align: right;
  }
  .person-name { font-size: 22px; color: var(--silver); font-weight: 400; }
  .person-name .first { font-weight: 700; }
  .person-role { font-size: 13px; color: var(--text-muted); letter-spacing: 0.06em; }
  .corner-mark {
    position: absolute; right: 34px; bottom: 30px;
    font-size: 15px; font-weight: 500; letter-spacing: 0.08em;
    text-transform: uppercase; color: var(--silver-soft);
  }

  /* Front: company side */
  .card-front {
    display: flex; align-items: center; justify-content: center; gap: 16px;
  }
  .card-front .brand-dot { width: 44px; height: 44px; }
  .front-name {
    font-size: 34px; font-weight: 500; letter-spacing: 0.08em;
    text-transform: uppercase; color: var(--silver);
  }
</style>
</head>
<body>
<main class="canvas">
  <section class="card card-back" aria-label="Business card, details side">
    <div class="brand"><span class="brand-dot"></span>Ward Compass</div>
    <p class="address">14 Annakhil<br>7 H.R.B. Rabat, Morocco</p>
    <ul class="contacts">
      <li><svg viewBox="0 0 12 12"><path d="M3 1.5l2 2.2-1.2 1.3a6 6 0 0 0 3.2 3.2l1.3-1.2 2.2 2-1.3 1.5C5.5 10.3 1.7 6.5 1.5 2.8z"/></svg>+90 612 348 2175</li>
      <li><svg viewBox="0 0 12 12"><rect x="1" y="2.5" width="10" height="7"/><path d="M1 2.5l5 4 5-4"/></svg>info@wardcompass.example</li>
      <li><svg viewBox="0 0 12 12"><circle cx="6" cy="6" r="4.8"/><path d="M1.2 6h9.6M6 1.2c-2.4 2.6-2.4 7 0 9.6M6 1.2c2.4 2.6 2.4 7 0 9.6"/></svg>www.wardcompass.example</li>
    </ul>
    <div class="person">
      <p class="person-name"><span class="first">Salwa</span> Kettani</p>
      <p class="person-role">CEO</p>
    </div>
    <div class="corner-mark">Ward Compass</div>
  </section>

  <section class="card card-front" aria-label="Business card, company side">
    <span class="brand-dot"></span>
    <span class="front-name">Ward Compass</span>
  </section>
</main>
</body>
</html>
```